Fernwick Landscaping Folder Design

I need a graphic designer to design a folder so we can insert informational sheets inside it for customers. The folder must include the company logo, project images, on front and back of folder and slogan " The Experience You Want, The Service You Expect, And The Value You Deserve'

Folder to also include phone numbers : 416 555 0193 as well as the website: www.fernwicklandscaping.example as well as we gurantee a 24 month warranty.

I have attached sample of size we need.

Pixel Harbor has also done something similar for me for Tollbridge Landscapes

Target Market(s)

geared toward home owners & commercial/industrial

Industry/Entity Type

Landscaping

Font styles to use
Other font styles liked:
• open to new trendy font

Requirements
Must have
• Telephone Number, email address, slogan, images,
Nice to have
• images of completed projects incorporated into the front and back of folder as well as the logo
Should not have
• n/a

```html
<!DOCTYPE html>
<html lang="en">
<head>
<meta charset="utf-8">
<title>Fernwick Landscaping Folder</title>
<link href="https://fonts.googleapis.com/css2?family=Oswald:wght@400;500;700&family=Roboto:wght@400;500&display=swap" rel="stylesheet">
<style>
  :root {
    --stage: #ebe9e6;
    --paper: #ffffff;
    --ink: #3d3d3d;
    --ink-soft: #6b6b6b;
    --hex-grey: #d9d9d9;
    --band: #585858;
    --band-text: #ffffff;
  }
  * { margin: 0; padding: 0; box-sizing: border-box; }
  html, body { width: 1200px; height: 848px; overflow: hidden; background: var(--stage); }
  .canvas { position: relative; width: 1200px; height: 848px; }
  .folder-page {
    position: absolute; top: 127px; width: 420px; height: 594px;
    background: var(--paper); overflow: hidden;
    box-shadow: 0 4px 14px rgba(0,0,0,.18);
  }
  .folder-front { left: 150px; }
  .folder-back { left: 630px; }
  .page-art { position: absolute; inset: 0; }

  .brand {
    position: absolute; left: 34px; top: 462px; width: 160px;
    font-family: "Oswald", sans-serif; color: var(--ink-soft); text-align: center;
  }
  .brand-name { font-size: 30px; font-weight: 500; letter-spacing: 2px; line-height: 1; }
  .brand-sub { font-size: 13px; font-weight: 500; letter-spacing: 3px; margin-top: 4px; }

  .slogan {
    position: absolute; left: 220px; top: 440px;
    font-family: "Oswald", sans-serif; font-weight: 700; font-size: 15px;
    line-height: 1.2; color: var(--ink); text-transform: uppercase; letter-spacing: .3px;
  }

  .warranty-band {
    position: absolute; left: 0; top: 470px; width: 100%; height: 22px;
    background: var(--band); color: var(--band-text);
    font-family: "Roboto", sans-serif; font-size: 9px; font-weight: 500; letter-spacing: .6px;
    display: flex; align-items: center; justify-content: center; text-transform: uppercase;
  }
  .contact-list {
    position: absolute; left: 0; top: 506px; width: 100%; list-style: none;
    font-family: "Roboto", sans-serif; font-size: 10px; color: var(--ink);
    display: flex; flex-direction: column; align-items: center; gap: 5px;
  }
  .contact-item { display: flex; align-items: center; gap: 6px; }
  .contact-icon { width: 9px; height: 9px; }
</style>
</head>
<body>
<div class="canvas">

  <section class="folder-page folder-front">
    <svg class="page-art" width="420" height="594" viewBox="0 0 420 594">
      <defs>
        <linearGradient id="drivewayPhoto" x1="0" y1="0" x2="0.3" y2="1">
          <stop offset="0" stop-color="#8a9278"/>
          <stop offset="0.35" stop-color="#5d6e44"/>
          <stop offset="0.6" stop-color="#c9cbc8"/>
          <stop offset="1" stop-color="#9c9e9c"/>
        </linearGradient>
        <linearGradient id="leftFade" x1="0" y1="0" x2="1" y2="0">
          <stop offset="0" stop-color="#ffffff" stop-opacity=".7"/>
          <stop offset="0.3" stop-color="#ffffff" stop-opacity="0"/>
        </linearGradient>
      </defs>
      <g role="img" aria-label="Photo of a curved concrete driveway in front of a house with autumn trees">
        <rect x="0" y="0" width="420" height="440" fill="url(#drivewayPhoto)"/>
        <rect x="0" y="0" width="420" height="440" fill="url(#leftFade)"/>
      </g>
      <path d="M0 430 C 90 430 160 380 230 340 C 300 300 360 300 420 320 L420 594 L0 594 Z" fill="var(--paper)"/>
    </svg>
    <div class="brand">
      <div class="brand-name">FERNWICK</div>
      <div class="brand-sub">LANDSCAPING LTD.</div>
    </div>
    <p class="slogan">The experience you want,<br>the service you expect,<br>and the value you deserve</p>
  </section>

  <section class="folder-page folder-back">
    <svg class="page-art" width="420" height="594" viewBox="0 0 420 594">
      <defs>
        <polygon id="hexCell" points="0,50 30,0 120,0 150,50 120,100 30,100"/>
        <linearGradient id="pourPhoto" x1="0" y1="0" x2="0" y2="1"><stop offset="0" stop-color="#b7b9b6"/><stop offset="1" stop-color="#8c8f89"/></linearGradient>
        <linearGradient id="poolPhoto" x1="0" y1="0" x2="1" y2="1"><stop offset="0" stop-color="#3f4a2f"/><stop offset="0.5" stop-color="#3d8fd6"/><stop offset="1" stop-color="#4d5a3a"/></linearGradient>
        <linearGradient id="treePhoto" x1="0" y1="0" x2="1" y2="1"><stop offset="0" stop-color="#3a3c36"/><stop offset="1" stop-color="#a9aaa6"/></linearGradient>
        <linearGradient id="drivePhoto" x1="0" y1="0" x2="0" y2="1"><stop offset="0" stop-color="#6b7a4c"/><stop offset="0.4" stop-color="#c9cac7"/><stop offset="1" stop-color="#b3b4b1"/></linearGradient>
        <linearGradient id="patioPhoto" x1="0" y1="0" x2="1" y2="1"><stop offset="0" stop-color="#6d7a52"/><stop offset="1" stop-color="#a6a39a"/></linearGradient>
        <linearGradient id="garagePhoto" x1="0" y1="0" x2="0" y2="1"><stop offset="0" stop-color="#dcd8cf"/><stop offset="1" stop-color="#a89680"/></linearGradient>
        <linearGradient id="bottomFade" x1="0" y1="0" x2="0" y2="1"><stop offset="0" stop-color="#fff" stop-opacity="0"/><stop offset="1" stop-color="#fff" stop-opacity="1"/></linearGradient>
      </defs>
      <g class="hex-grid" fill="var(--hex-grey)" stroke="var(--paper)" stroke-width="6">
        <use href="#hexCell" x="-40" y="-20"/><use href="#hexCell" x="-40" y="80"/><use href="#hexCell" x="-40" y="180"/><use href="#hexCell" x="-40" y="280"/><use href="#hexCell" x="-40" y="380"/>
        <use href="#hexCell" x="80" y="-70"/><use href="#hexCell" x="80" y="130"/><use href="#hexCell" x="80" y="330"/><use href="#hexCell" x="80" y="430"/>
        <use href="#hexCell" x="200" y="-20"/><use href="#hexCell" x="200" y="180"/><use href="#hexCell" x="200" y="380"/>
        <use href="#hexCell" x="320" y="-70"/><use href="#hexCell" x="320" y="130"/><use href="#hexCell" x="320" y="330"/><use href="#hexCell" x="320" y="430"/>
        <use href="#hexCell" x="440" y="-20"/>
        <use href="#hexCell" x="80" y="30" fill="url(#pourPhoto)" role="img" aria-label="Photo of workers finishing a concrete pour"/>
        <use href="#hexCell" x="200" y="80" fill="url(#poolPhoto)" role="img" aria-label="Photo of a backyard pool lit at dusk"/>
        <use href="#hexCell" x="320" y="30" fill="url(#treePhoto)" role="img" aria-label="Photo of trees beside a paved yard"/>
        <use href="#hexCell" x="320" y="230" fill="url(#drivePhoto)" role="img" aria-label="Photo of a finished concrete driveway"/>
        <use href="#hexCell" x="80" y="230" fill="url(#patioPhoto)" role="img" aria-label="Photo of a stone patio with garden planting"/>
        <use href="#hexCell" x="200" y="280" fill="url(#garagePhoto)" role="img" aria-label="Photo of an interlock entrance by a garage"/>
      </g>
      <rect x="0" y="380" width="420" height="90" fill="url(#bottomFade)"/>
    </svg>
    <div class="warranty-band">We gurantee a 24 month warranty</div>
    <ul class="contact-list">
      <li class="contact-item">
        <svg class="contact-icon" viewBox="0 0 10 10"><circle cx="5" cy="5" r="5" fill="var(--ink)"/><path d="M3.2 2.6l1 .9-.5.8c.4.8.9 1.3 1.7 1.7l.8-.5.9 1-.7.8C4.6 7.1 2.9 5.4 2.5 3.3z" fill="#fff"/></svg>
        <span>416 555 0193</span>
      </li>
      <li class="contact-item">
        <svg class="contact-icon" viewBox="0 0 10 10"><circle cx="5" cy="5" r="5" fill="var(--ink)"/><circle cx="5" cy="5" r="2.8" fill="none" stroke="#fff" stroke-width=".8"/><path d="M2.2 5h5.6M5 2.2v5.6" stroke="#fff" stroke-width=".6"/></svg>
        <span>www.fernwicklandscaping.example</span>
      </li>
    </ul>
  </section>

</div>
</body>
</html>
```